Velmarotix - world unique technology for better life - please let them know who am i at first sight

We need a new business card for company which is a provider of unique crystal based technology suitable for all living being. For more information and final design you can use our brochure (our colours are black and blue from brochure).
We use Verdana font

Industry/Entity Type

Business

Contact Information for Business Card

regular dimension

Font styles to use
Other font styles liked:
• Verdana

Requirements
Must have
• Logo
• name
• function/position
• phone
• mobile
• e-mail
• adress
Nice to have
• inovative design (technology directed)

```html
<!DOCTYPE html>
<html lang="en">
<head>
<meta charset="utf-8">
<title>Velmarotix business card</title>
<link rel="stylesheet" href="https://fonts.googleapis.com/css2?family=Open+Sans:wght@300;400;600&display=swap">
<style>
  :root {
    --page-bg: #e9ecef;
    --card-white: #ffffff;
    --card-shade: #eef0f2;
    --blue-light: #5fd0ee;
    --blue: #27b6e0;
    --blue-deep: #1592c6;
    --ink: #1f1f1f;
    --graphite: #3a3a3a;
    --swoosh-grey: #9a9a9a;
    --name-brown: #6d5a52;
    --position-white: #eaf8fd;
  }
  * { margin: 0; padding: 0; box-sizing: border-box; }
  html, body { width: 1200px; height: 858px; overflow: hidden; }
  body {
    background: var(--page-bg);
    font-family: "Open Sans", Verdana, sans-serif;
    position: relative;
  }
  .card {
    position: absolute;
    width: 540px;
    height: 309px;
    top: 275px;
    border-radius: 3px;
    overflow: hidden;
    box-shadow: 0 6px 18px rgba(0,0,0,0.18);
  }
  .card--front { left: 40px; background: linear-gradient(180deg, var(--card-white), var(--card-shade)); }
  .card--back { left: 620px; background: radial-gradient(ellipse at 40% 35%, var(--blue-light), var(--blue) 45%, var(--blue-deep)); }

  .front-bands { position: absolute; inset: 0; }

  .brand {
    position: absolute;
    display: flex;
    align-items: center;
    gap: 12px;
  }
  .brand__dot { border-radius: 50%; flex: none; }
  .brand__name { font-weight: 300; letter-spacing: 2px; line-height: 1; }

  .card--front .brand { left: 34px; top: 40px; }
  .card--front .brand__dot { width: 44px; height: 44px; background: var(--blue); }
  .card--front .brand__name { font-size: 32px; color: var(--blue); }

  .address {
    position: absolute;
    right: 34px;
    top: 104px;
    text-align: right;
    font-size: 13px;
    line-height: 18px;
    color: var(--ink);
  }
  .contacts {
    position: absolute;
    right: 34px;
    top: 150px;
    list-style: none;
    font-size: 13px;
    line-height: 19px;
    color: var(--ink);
  }
  .contacts li { display: flex; justify-content: flex-end; align-items: center; gap: 8px; }
  .contacts svg { width: 12px; height: 12px; flex: none; }

  .person {
    position: absolute;
    left: 34px;
    bottom: 26px;
  }
  .person__name { font-size: 22px; font-weight: 600; color: var(--name-brown); line-height: 1.1; }
  .person__position { font-size: 14px; color: var(--position-white); }

  .card--back .brand { left: 50%; top: 50%; transform: translate(-50%, -50%); gap: 16px; }
  .card--back .brand__dot { width: 60px; height: 60px; background: var(--card-white); }
  .card--back .brand__name { font-size: 44px; color: var(--card-white); }
</style>
</head>
<body>

<section class="card card--front" aria-label="Card front">
  <svg class="front-bands" viewBox="0 0 540 309" preserveAspectRatio="none" aria-hidden="true">
    <defs>
      <linearGradient id="front-blue" x1="0" y1="0" x2="0" y2="1">
        <stop offset="0" stop-color="#5fd0ee"/>
        <stop offset="1" stop-color="#1ea7d8"/>
      </linearGradient>
    </defs>
    <path d="M0 190 Q150 300 540 240 L540 309 L0 309 Z" fill="url(#front-blue)"/>
    <path d="M0 176 Q150 290 540 236 Q150 280 0 190 Z" fill="#3a3a3a"/>
    <path d="M0 184 Q150 292 540 240 Q150 286 0 192 Z" fill="#9a9a9a"/>
  </svg>

  <div class="brand">
    <span class="brand__dot" aria-hidden="true"></span>
    <span class="brand__name">VELMAROTIX</span>
  </div>

  <p class="address">22-28 Harrow Lane<br>London N7 3QD, United Kingdom</p>

  <ul class="contacts">
    <li>+ xxx(x) xx xxx xxx
      <svg viewBox="0 0 12 12" aria-label="Mobile"><rect x="3" y="0.5" width="6" height="11" rx="1" fill="#27b6e0"/><rect x="4" y="2" width="4" height="6" fill="#fff"/></svg>
    </li>
    <li>+385(0) 21 447 903
      <svg viewBox="0 0 12 12" aria-label="Phone"><path d="M1 4 Q6 0 11 4 L9 5.5 L8 4 L4 4 L3 5.5 Z" fill="#27b6e0"/><rect x="2.5" y="6" width="7" height="5" rx="1" fill="#27b6e0"/></svg>
    </li>
    <li>info@velmarotix.eu
      <svg viewBox="0 0 12 12" aria-label="Email"><rect x="0.5" y="2.5" width="11" height="7" fill="#27b6e0"/><path d="M0.5 2.5 L6 7 L11.5 2.5" fill="none" stroke="#fff" stroke-width="1"/></svg>
    </li>
    <li>www.velmarotix.eu
      <svg viewBox="0 0 12 12" aria-label="Website"><circle cx="6" cy="6" r="5.3" fill="#27b6e0"/><path d="M0.7 6 H11.3 M6 0.7 V11.3" stroke="#fff" stroke-width="0.9"/><ellipse cx="6" cy="6" rx="2.4" ry="5.3" fill="none" stroke="#fff" stroke-width="0.9"/></svg>
    </li>
  </ul>

  <div class="person">
    <p class="person__name">Employee Name</p>
    <p class="person__position">Employee Position</p>
  </div>
</section>

<section class="card card--back" aria-label="Card back">
  <div class="brand">
    <span class="brand__dot" aria-hidden="true"></span>
    <span class="brand__name">VELMAROTIX</span>
  </div>
</section>

</body>
</html>
```